Business Card - high end, modern health care

Hey designers!

We need a double sided business card for the boutique, cutting edge physical therapy rehabilitation centre in Sydney's Northern Beaches.

With the most qualified physios in the area The Harbourview Motion Clinic does what other physiotherapy practices do not, we take our time with our patients giving them longer appointments, better physios and therefor faster results!

We guarantee that the service people receive at THMC will be unparalleled.

Hence we need a business card to reflect our modern, boutique, high end service. The final design needs to reflect that we are in a class of our own yet with the feel of beachside retreat.

Below I have attached our logo in both blue on white and white on blue. The exact colour is;
and the font that we have used in our logo is Tex Gyre Aventador.

I like the idea of the blue as the main colour as it is more eye catching and our signage onto the main road will be in this blue and in the interest of consistency across marketing the blue needs to be a part of the design. However I would appreciate a few designs onto a wooden background as this is a visual theme within the fitout of the practice.

The design needs to be of standard size (91x55mm).

Target Market(s)

We target people who have an end outcome in mind and those who have had poor experiences with other providers and ensure that everyone gets the care that they deserve with a premium service that is tailored to the individuals circumstances. As a premium service, the target market is highly educated, business and tech savvy with the additional target market of elderly people who have self funded their retirement and see value in paying for the best ongoing rehabilitation to maintain independence.

Industry/Entity Type

Physical Therapy

Contact Information for Business Card

Name, designation( Titled Musculoskeletal Physiotherapist... there will also be those in the company that have multiple designations ie 5 or 6 words long), phone number, email, facebook, instagram, address

Font styles to use
Sans Serif

Colors

Designer to choose colors to be used in the design.

Requirements
Must have
• Front - The logo as large as possible, blue or wooden theme, and all of the important details.
• Back - A blank space/lines on which to write appointment times (no "Appointment, date, time" etc.)
Nice to have
• facebook url
• logos for facebook and instagram
• Mini logos for the phone and email?

```html
<!DOCTYPE html>
<html lang="en">
<head>
<meta charset="utf-8">
<title>The Harbourview Motion Clinic – Business Card</title>
<link rel="stylesheet" href="https://fonts.googleapis.com/css2?family=Roboto:wght@400;700&family=Source+Sans+3:wght@400&display=swap">
<style>
  :root {
    --brand-blue: #0453a4;
    --canvas-bg: #2b2b2b;
    --card-white: #ffffff;
    --card-paper: #f3f3f3;
    --ink-grey: #555555;
    --rule-grey: #6d6d6d;
  }
  * { box-sizing: border-box; margin: 0; padding: 0; }
  html, body {
    width: 1200px; height: 960px; overflow: hidden;
    background: var(--canvas-bg);
  }
  .canvas { position: relative; width: 1200px; height: 960px; }

  .card {
    position: absolute;
    width: 598px; height: 342px;
    border-radius: 16px;
    overflow: hidden;
  }

  /* Front */
  .card-front { left: 322px; top: 108px; background: var(--card-paper); font-family: "Roboto", sans-serif; }
  .brand-panel { position: absolute; left: 0; top: 0; width: 598px; height: 342px; }
  .brand-mark {
    position: absolute; left: 290px; top: 130px; width: 270px;
    text-align: center;
    font-size: 24px; font-weight: 700; line-height: 30px;
    color: var(--card-white); text-transform: uppercase; letter-spacing: 0.5px;
  }
  .person-name {
    position: absolute; left: 27px; top: 34px;
    font-size: 21px; font-weight: 700; color: var(--brand-blue);
    letter-spacing: -0.2px;
  }
  .person-role {
    position: absolute; left: 27px; top: 60px;
    font-size: 14px; color: var(--ink-grey);
  }
  .address {
    position: absolute; left: 27px; top: 109px;
    font-size: 14px; line-height: 18px; color: var(--ink-grey);
  }
  .contact-list {
    position: absolute; left: 27px; top: 155px;
    list-style: none;
  }
  .contact-item {
    display: flex; align-items: center;
    height: 19px; font-size: 14px; color: var(--ink-grey);
  }
  .contact-icon { width: 13px; height: 13px; margin-right: 10px; flex: none; }
  .wordmark {
    position: absolute; left: 27px; top: 262px;
    font-size: 19px; font-weight: 700; line-height: 22px;
    color: var(--brand-blue); text-transform: uppercase; letter-spacing: 0.3px;
  }

  /* Back */
  .card-back { left: 320px; top: 493px; background: var(--card-white); font-family: "Source Sans 3", sans-serif; }
  .appt-field {
    position: absolute; font-size: 17px; color: var(--ink-grey); line-height: 1;
  }
  .rule { position: absolute; height: 1px; background: var(--rule-grey); }
</style>
</head>
<body>
<main class="canvas">

  <section class="card card-front" aria-label="Business card front">
    <svg class="brand-panel" viewBox="0 0 598 342" aria-hidden="true">
      <circle cx="423" cy="172" r="178" fill="var(--brand-blue)"/>
      <rect x="423" y="0" width="175" height="342" fill="var(--brand-blue)"/>
    </svg>
    <p class="brand-mark" role="img" aria-label="The Harbourview Motion Clinic logo">The Harbourview<br>Motion<br>Clinic</p>

    <h1 class="person-name">DANIEL REYES</h1>
    <p class="person-role">CEO/FOUNDER</p>

    <p class="address">42 Pittwater Crescent<br>Collaroy, NSW 2097</p>

    <ul class="contact-list">
      <li class="contact-item">
        <svg class="contact-icon" viewBox="0 0 16 16"><path fill="var(--brand-blue)" d="M3.2 1.2l2.4-.4 1.6 3.6-1.5 1.2c.8 1.9 2.3 3.4 4.2 4.2l1.2-1.5 3.6 1.6-.4 2.4c-.2.9-1 1.5-1.9 1.5C6.6 13.8 2.2 9.4 1.7 3.1c0-.9.6-1.7 1.5-1.9z"/></svg>
        02 9555 0148
      </li>
      <li class="contact-item">
        <svg class="contact-icon" viewBox="0 0 16 16"><rect x="1" y="3" width="14" height="10" fill="var(--brand-blue)"/><path d="M1.5 3.5L8 9l6.5-5.5" fill="none" stroke="#f3f3f3" stroke-width="1.4"/></svg>
        daniel@hvmc.com.au
      </li>
      <li class="contact-item">
        <svg class="contact-icon" viewBox="0 0 16 16"><circle cx="8" cy="8" r="6.5" fill="none" stroke="var(--brand-blue)" stroke-width="1.6"/><ellipse cx="8" cy="8" rx="2.8" ry="6.5" fill="none" stroke="var(--brand-blue)" stroke-width="1.3"/><path d="M1.5 8h13" stroke="var(--brand-blue)" stroke-width="1.3"/></svg>
        www.hvmc.com.au
      </li>
      <li class="contact-item">
        <svg class="contact-icon" viewBox="0 0 16 16"><rect x="1.5" y="1.5" width="13" height="13" fill="var(--brand-blue)"/></svg>
        /hvmotionclinic
      </li>
      <li class="contact-item">
        <svg class="contact-icon" viewBox="0 0 16 16"><circle cx="8" cy="8" r="6.5" fill="var(--brand-blue)"/></svg>
        @hvmotionclinic
      </li>
    </ul>

    <p class="wordmark">The Harbourview<br>Motion Clinic</p>
  </section>

  <section class="card card-back" aria-label="Business card back, appointment lines">
    <span class="appt-field" style="left:32px; top:43px;">Name</span>
    <span class="rule" style="left:80px; top:56px; width:478px;"></span>

    <span class="appt-field" style="left:32px; top:86px;">Date</span>
    <span class="rule" style="left:72px; top:99px; width:261px;"></span>
    <span class="appt-field" style="left:340px; top:86px;">Time</span>
    <span class="rule" style="left:383px; top:99px; width:115px;"></span>
    <span class="appt-field" style="left:503px; top:86px;">am/pm</span>

    <span class="rule" style="left:35px; top:139px; width:523px;"></span>
    <span class="rule" style="left:35px; top:179px; width:523px;"></span>
    <span class="rule" style="left:35px; top:219px; width:523px;"></span>
    <span class="rule" style="left:35px; top:259px; width:523px;"></span>
    <span class="rule" style="left:35px; top:299px; width:523px;"></span>
  </section>

</main>
</body>
</html>
```